Postcard design to acquire new clients for my Property Management Company

I'm looking for a postcard design that I can send to prospective clients detailing information about my company and services.
Postcard should be eye catching and contain information from www.bramblecrestpm.com. I've provided a few screen shots for the most important information and my logo.
Target Market(s)
Real Estate
Industry/Entity Type
Real Estate
Font styles to use
Sans Serif
Requirements
Must have
- Must be eye catching!! this will be a direct mail piece - I'd like for the card to be read and not tossed in the trash immediately.
Design que from the logo.
A place to write / print the receipts name and address.
our physical address - 2387 Hollow Pine Road, Lubbock, TX 79852.
Should not have
- the contact information on the business card is not accurate - please use info from website.

```html
<!DOCTYPE html>
<html lang="en">
<head>
<meta charset="utf-8">
<title>Bramblecrest Property Management Postcard</title>
<link href="https://fonts.googleapis.com/css2?family=Fira+Sans:wght@500&family=Montserrat:wght@400;500;600;700;800&display=swap" rel="stylesheet">
<style>
  :root {
    --brand-blue: #1b5592;
    --ink: #111111;
    --text-grey: #444444;
    --band-grey: #b4b4b4;
    --paper: #ffffff;
    --backdrop: #606060;
    --sky-top: #8fb6de;
    --sky-bottom: #d8e4ee;
    --rule: #222222;
  }
  * { box-sizing: border-box; margin: 0; padding: 0; }
  html, body { width: 1200px; height: 564px; overflow: hidden; }
  body {
    background: var(--backdrop);
    font-family: "Montserrat", sans-serif;
    position: relative;
  }
  .card {
    position: absolute;
    top: 103px;
    width: 523px;
    background: var(--paper);
    box-shadow: 0 8px 20px rgba(0,0,0,0.35);
    overflow: hidden;
  }

  /* Front */
  .card--front { left: 50px; height: 348px; }
  .front-art { position: absolute; left: 0; top: 0; width: 523px; height: 308px; }
  .brand-name {
    position: absolute; left: 6px; top: 8px;
    font-family: "Montserrat", sans-serif; font-weight: 700;
    color: var(--brand-blue); letter-spacing: 3px;
    font-size: 11.5px; line-height: 15px;
  }
  .headline { position: absolute; left: 5px; top: 76px; white-space: nowrap; }
  .headline__property {
    font-weight: 800; font-size: 49px; line-height: 48px;
    color: var(--ink); letter-spacing: -1px;
  }
  .headline__management {
    font-weight: 700; font-size: 33px; line-height: 36px;
    color: var(--brand-blue); margin-top: 3px;
  }
  .headline__area {
    font-weight: 600; font-size: 26px; line-height: 34px;
    color: var(--ink); letter-spacing: -0.5px;
  }
  .divider {
    position: absolute; left: 99px; top: 213px;
    width: 68px; height: 2px; background: var(--brand-blue);
  }
  .tagline {
    position: absolute; left: 5px; top: 232px;
    font-size: 13px; line-height: 16px; color: var(--text-grey); font-weight: 500;
  }
  .contact-bar {
    position: absolute; left: 0; bottom: 0; width: 523px; height: 40px;
    background: var(--brand-blue); display: flex; align-items: center;
    color: var(--paper); font-size: 13.5px; font-weight: 500; white-space: nowrap;
    padding-right: 12px;
  }
  .contact-bar__label {
    flex: 0 0 138px; height: 100%; background: var(--band-grey);
    color: var(--ink); font-weight: 700; font-size: 16.5px;
    display: flex; align-items: center; padding-left: 9px;
  }
  .contact-bar__item { display: flex; align-items: center; gap: 6px; }
  .contact-bar__item--phone { margin-left: 18px; }
  .contact-bar__item--email { margin-left: auto; }

  /* Back */
  .card--back { left: 624px; height: 345px; }
  .services-heading {
    position: absolute; left: 0; top: 8px; width: 311px; height: 21px;
    background: var(--brand-blue); color: var(--paper);
    font-weight: 800; font-size: 14.5px; text-align: center; line-height: 21px;
  }
  .service { position: absolute; width: 130px; }
  .service__icon { position: absolute; left: -29px; top: -1px; width: 22px; height: 22px; fill: var(--brand-blue); }
  .service__title {
    font-family: "Fira Sans", sans-serif; font-weight: 500;
    color: var(--brand-blue); font-size: 12px; line-height: 14px; white-space: nowrap;
  }
  .service__body {
    font-size: 6.9px; line-height: 7.2px; color: var(--ink); font-weight: 500;
    margin-top: 2px; width: 118px; letter-spacing: -0.1px;
  }
  .closing-band {
    position: absolute; left: 0; top: 274px; width: 311px; height: 71px;
    background: var(--brand-blue); color: var(--paper);
    font-weight: 600; font-size: 15.5px; line-height: 19px; text-align: center;
    padding-top: 13px;
  }
  .return-address {
    position: absolute; left: 329px; top: 12px;
    font-size: 7.5px; line-height: 10px; color: var(--ink); font-weight: 500;
  }
  .return-address__name { color: var(--brand-blue); font-weight: 700; }
  .stamp-box {
    position: absolute; left: 436px; top: 9px; width: 74px; height: 79px;
    border: 1.5px solid var(--rule);
  }
  .address-line {
    position: absolute; left: 329px; width: 181px; height: 1px; background: var(--rule);
  }
</style>
</head>
<body>

<section class="card card--front">
  <svg class="front-art" viewBox="0 0 523 308">
    <defs>
      <linearGradient id="sky" x1="0" y1="0" x2="0" y2="1">
        <stop offset="0" stop-color="var(--sky-top)"/>
        <stop offset="0.55" stop-color="var(--sky-bottom)"/>
        <stop offset="1" stop-color="#7d8794"/>
      </linearGradient>
    </defs>
    <rect role="img" aria-label="Photo of a modern white multi-storey house with dark balconies and glass railings under a blue sky" x="200" y="0" width="323" height="308" fill="url(#sky)"/>
    <path d="M0 0 H240 C330 90 310 230 225 308 H0 Z" fill="var(--paper)"/>
    <path d="M240 0 C330 90 310 230 225 308" fill="none" stroke="var(--brand-blue)" stroke-width="2"/>
  </svg>

  <div class="brand-name">BRAMBLECREST<br>PROPERTY MANAGEMENT</div>

  <div class="headline">
    <div class="headline__property">PROPERTY</div>
    <div class="headline__management">MANAGEMENT</div>
    <div class="headline__area">ACROSS LUBBOCK</div>
  </div>
  <div class="divider"></div>
  <p class="tagline">Maximize your financial returns with<br>support from our rental specialists</p>

  <div class="contact-bar">
    <div class="contact-bar__label">Get In Touch</div>
    <div class="contact-bar__item contact-bar__item--phone">
      <svg width="14" height="14" viewBox="0 0 24 24" fill="var(--paper)"><path d="M6.6 10.8a15.1 15.1 0 0 0 6.6 6.6l2.2-2.2a1 1 0 0 1 1-.25 11.4 11.4 0 0 0 3.6.57 1 1 0 0 1 1 1V20a1 1 0 0 1-1 1A17 17 0 0 1 3 4a1 1 0 0 1 1-1h3.5a1 1 0 0 1 1 1c0 1.25.2 2.45.57 3.6a1 1 0 0 1-.25 1z"/></svg>
      <span>(806) 555-0147</span>
    </div>
    <div class="contact-bar__item contact-bar__item--email">
      <svg width="17" height="12" viewBox="0 0 18 13" fill="none" stroke="var(--paper)" stroke-width="1.4"><rect x="0.7" y="0.7" width="16.6" height="11.6"/><path d="M0.7 0.7 9 7.5 17.3 0.7M0.7 12.3 7 6.2M17.3 12.3 11 6.2"/></svg>
      <span>info@bramblecrestpm.com</span>
    </div>
  </div>
</section>

<section class="card card--back">
  <h2 class="services-heading">OUR SERVICES</h2>

  <div class="service" style="left:35px;top:44px">
    <svg class="service__icon" viewBox="0 0 24 24"><path d="M12 3 1 12h3v9h6v-6h4v6h6v-9h3z"/></svg>
    <div class="service__title">Property Marketing</div>
    <p class="service__body" style="font-size:7.4px;line-height:8.4px">Let us take over your marketing for you and we'll find a quali-fied renter quickly.</p>
  </div>
  <div class="service" style="left:36px;top:93px">
    <svg class="service__icon" viewBox="0 0 24 24"><circle cx="8" cy="7" r="4"/><circle cx="17" cy="8" r="3.3"/><path d="M0 20c0-5 3.5-7 8-7s8 2 8 7zM17 13c4 0 7 2 7 6h-6.5c0-2.5-.8-4.4-2.5-5.7z"/></svg>
    <div class="service__title">Tenant Screening</div>
    <p class="service__body">We don't just find someone to rent your home—we find the best renters. We screen all ap-plications using fair housing guidelines to protect you.</p>
  </div>
  <div class="service" style="left:36px;top:149px">
    <svg class="service__icon" viewBox="0 0 24 24"><text x="6" y="21" font-family="Montserrat, sans-serif" font-weight="700" font-size="22" fill="var(--brand-blue)">$</text></svg>
    <div class="service__title">Rent Collection</div>
    <p class="service__body">Stop guessing when you'll re-ceive your rental earnings every month and say hello to consis-tent payments. We keep your tenants current.</p>
  </div>
  <div class="service" style="left:36px;top:207px">
    <svg class="service__icon" viewBox="0 0 24 24"><path d="M13 3l6 6-3 3-2-2-9 11-2-2 11-9-2-2z"/></svg>
    <div class="service__title">Maintenance</div>
    <p class="service__body">Still scrambling to respond to repair requests every time you receive a tenant call? Let us co-ordinate repair work on your behalf!</p>
  </div>

  <div class="service" style="left:180px;top:42px">
    <svg class="service__icon" viewBox="0 0 24 24"><circle cx="10" cy="10" r="6.5" fill="none" stroke="var(--brand-blue)" stroke-width="3"/><path d="M14.5 14.5 21 21" stroke="var(--brand-blue)" stroke-width="3.5"/></svg>
    <div class="service__title">Property Inspections</div>
    <p class="service__body">We visit every home in our portfolio regularly.</p>
  </div>
  <div class="service" style="left:180px;top:84px">
    <svg class="service__icon" viewBox="0 0 24 24"><path d="M2 3h1.6v17H22v1.6H2z"/><rect x="6" y="12" width="2" height="6"/><rect x="10" y="8" width="2" height="10"/><rect x="14" y="11" width="2" height="7"/><rect x="18" y="6" width="2" height="12"/></svg>
    <div class="service__title">Financial Reporting</div>
    <p class="service__body">Keep a handle on your real estate performance. We generate monthly statements so you can review income &amp; expenses at a moment's notice.</p>
  </div>
  <div class="service" style="left:180px;top:144px">
    <svg class="service__icon" viewBox="0 0 24 24"><path d="M12 1 3 4.5v6c0 6 4 10.5 9 12.5 5-2 9-6.5 9-12.5v-6zm0 2.3v17.4c-3.8-1.8-6.6-5.4-6.6-10.2V6.1z"/></svg>
    <div class="service__title">Evictions</div>
    <p class="service__body">When things go wrong inside your rental home, rest easy with the experts on your side. We will handle evictions for you &amp; find new renters when its over.</p>
  </div>
  <div class="service" style="left:180px;top:205px">
    <svg class="service__icon" viewBox="0 0 24 24"><path d="M11 3h2v16h5v2H6v-2h5zM3 6h18v1.6H3z"/><path d="M5 7.5 2 14h6zM19 7.5 16 14h6z" fill="none" stroke="var(--brand-blue)" stroke-width="1.4"/><path d="M2 14h6a3 2 0 0 1-6 0zM16 14h6a3 2 0 0 1-6 0z"/></svg>
    <div class="service__title">Legal Guidance</div>
    <p class="service__body">Don't accidentally violate one of the many ordinances and hous-ing laws governing your relation-ship with your tenants. Let us keep you compliant.</p>
  </div>

  <div class="closing-band">CHOOSE THE RIGHT<br>PROPERTY MANAGEMENT SYSTEM</div>

  <address class="return-address" style="font-style:normal">
    <span class="return-address__name">Bramblecrest Property Management</span><br>
    2387 Hollow Pine Road<br>
    Lubbock, TX 79852
  </address>
  <div class="stamp-box"></div>
  <div class="address-line" style="top:127px"></div>
  <div class="address-line" style="top:178px"></div>
  <div class="address-line" style="top:229px"></div>
</section>

</body>
</html>
```